Realty Group Needs Classy, Contemporary Letterhead Design

We need a letterhead design for a new realty company located in NY, USA. We buy investment properties to rehabilitate and or keep in our rental portfolio.

```html
<!DOCTYPE html>
<html lang="en">
<head>
<meta charset="utf-8">
<title>Orionvale Realty Group – Letterhead</title>
<link rel="stylesheet" href="https://fonts.googleapis.com/css2?family=Montserrat:wght@400;500;800&display=swap">
<style>
  :root {
    --brand-purple: #523a7e;
    --header-grey: #d3d4d6;
    --paper: #ffffff;
    --watermark: #ececec;
    --muted-text: #7a7a7a;
    --footer-text: #ffffff;
  }
  html, body {
    margin: 0;
    padding: 0;
    width: 1000px;
    height: 1200px;
    overflow: hidden;
    background: var(--paper);
  }
  .letterhead {
    position: relative;
    width: 1000px;
    height: 1200px;
    background: var(--paper);
    font-family: "Montserrat", sans-serif;
    overflow: hidden;
  }
  .header-wave {
    position: absolute;
    top: 0;
    left: 0;
    width: 1000px;
    height: 220px;
  }
  .brand {
    position: absolute;
    left: 58px;
    top: 88px;
    width: 236px;
    text-align: center;
  }
  .brand-name {
    display: block;
    font-size: 37px;
    font-weight: 800;
    letter-spacing: -0.5px;
    line-height: 1;
    color: var(--brand-purple);
  }
  .brand-tagline {
    display: flex;
    align-items: center;
    gap: 6px;
    margin-top: 4px;
    font-size: 11px;
    font-weight: 500;
    letter-spacing: 1px;
    color: var(--muted-text);
  }
  .brand-tagline::before,
  .brand-tagline::after {
    content: "";
    flex: 1;
    height: 1px;
    background: var(--muted-text);
  }
  .address {
    position: absolute;
    right: 61px;
    top: 118px;
    text-align: right;
    font-size: 14px;
    line-height: 18px;
    color: var(--brand-purple);
  }
  .address-icon {
    width: 13px;
    height: 12px;
    vertical-align: -1px;
    margin-right: 4px;
    fill: var(--brand-purple);
  }
  .watermark {
    position: absolute;
    left: 270px;
    top: 370px;
    width: 440px;
    height: 440px;
    border-radius: 50%;
    background: var(--watermark);
  }
  .footer-band {
    position: absolute;
    left: 0;
    top: 1130px;
    width: 1000px;
    height: 49px;
    background: var(--brand-purple);
    display: flex;
    align-items: center;
    justify-content: center;
    color: var(--footer-text);
    font-size: 14px;
  }
  .contact-item {
    display: flex;
    align-items: center;
    gap: 6px;
    padding: 0 9px;
  }
  .contact-item + .contact-item {
    border-left: 1px solid rgba(255, 255, 255, 0.7);
  }
  .contact-icon {
    width: 11px;
    height: 11px;
    fill: none;
    stroke: var(--footer-text);
    stroke-width: 1.6;
  }
</style>
</head>
<body>
<main class="letterhead">
  <svg class="header-wave" viewBox="0 0 1000 220" aria-hidden="true">
    <path d="M0,0 H1000 V137 C985,160 950,180 900,190 C850,200 790,190 700,160 C560,110 420,33 266,33 C180,33 90,45 0,92 Z" fill="var(--header-grey)"/>
    <path d="M0,92 C90,45 180,33 266,33 C420,33 560,110 700,160 C790,190 850,200 900,190 C950,180 985,160 1000,137" fill="none" stroke="var(--brand-purple)" stroke-width="5"/>
  </svg>

  <div class="brand">
    <span class="brand-name">ORIONVALE</span>
    <span class="brand-tagline">Realty Group, LLC</span>
  </div>

  <address class="address" style="font-style: normal;">
    <svg class="address-icon" viewBox="0 0 13 12" aria-hidden="true"><path d="M6.5 0 L13 6 H11 V12 H8 V8 H5 V12 H2 V6 H0 Z"/></svg>00, xxxxxx, xxxxxxx<br>
    xxxxxxx-0000
  </address>

  <div class="watermark" role="img" aria-label="Faint large brand mark watermark"></div>

  <footer class="footer-band">
    <span class="contact-item">
      <svg class="contact-icon" viewBox="0 0 12 12" aria-hidden="true"><path d="M2 1 L4.5 1 L5.5 4 L4 5 C5 7 6 8 7.5 8.5 L8.5 7 L11 8 L11 10.5 C6 11 1 6 2 1 Z"/></svg>00 000 0000
    </span>
    <span class="contact-item">
      <svg class="contact-icon" viewBox="0 0 12 12" aria-hidden="true"><rect x="3" y="0.8" width="6" height="10.4" rx="1"/></svg>0000000000
    </span>
    <span class="contact-item">
      <svg class="contact-icon" viewBox="0 0 12 12" aria-hidden="true"><rect x="0.8" y="2.5" width="10.4" height="7" /><path d="M0.8 2.5 L6 6.5 L11.2 2.5"/></svg>xxxxx@xxxx.xxx
    </span>
    <span class="contact-item">
      <svg class="contact-icon" viewBox="0 0 12 12" aria-hidden="true"><circle cx="6" cy="6" r="5"/><ellipse cx="6" cy="6" rx="2.2" ry="5"/><path d="M1 6 H11"/></svg>xxx.xxxxxxxxxxxxx.xxx
    </span>
  </footer>
</main>
</body>
</html>
```